Simple and Clean business card design

We would like the design to be simple clean and to incorporate our colors.

We are open to your design and talent, we have the dots in our logo as we think of it as data points and we connect data points for people.

We are open to see the great creative and clean design you bring to the table

Contact Information for Business Card

please include: name, position, email, phone and website

Font styles to use
Sans Serif

Requirements
Must have
• my colors incorporated, simplicity
Nice to have
• lots of white space, simplicity
Should not have
• complexicity/ complex art

```html
<!DOCTYPE html>
<html lang="en">
<head>
<meta charset="utf-8">
<title>Nectra business card</title>
<link rel="stylesheet" href="https://fonts.googleapis.com/css2?family=Oswald:wght@500&family=Work+Sans:wght@400;600&display=swap">
<style>
  :root {
    --backdrop: #3b3b40;
    --card-dark: #050505;
    --card-light: #ffffff;
    --ink: #111111;
    --brand-blue: #5b7fc4;
    --logo-light: #ffffff;
  }
  * { box-sizing: border-box; margin: 0; padding: 0; }
  html, body { width: 1200px; height: 913px; overflow: hidden; }
  body {
    background: var(--backdrop);
    font-family: "Work Sans", sans-serif;
    position: relative;
  }
  .card {
    position: absolute;
    top: 296px;
    width: 540px;
    height: 320px;
    border-radius: 14px;
    overflow: hidden;
  }
  .card--back { left: 40px; background: var(--card-dark); }
  .card--front { left: 620px; background: var(--card-light); }

  .brand-name {
    position: absolute;
    font-family: "Work Sans", sans-serif;
    font-weight: 600;
    font-size: 72px;
    letter-spacing: 1px;
    line-height: 1;
  }
  .card--back .brand-name {
    color: var(--logo-light);
    left: 0; right: 0; top: 122px;
    text-align: center;
  }
  .card--front .brand-name {
    color: var(--ink);
    left: 170px; top: 62px;
    font-size: 64px;
  }

  .person {
    position: absolute;
    left: 40px;
    top: 196px;
    text-align: right;
  }
  .person__name {
    font-family: "Oswald", sans-serif;
    font-weight: 500;
    font-size: 40px;
    letter-spacing: 1px;
    color: var(--brand-blue);
    line-height: 1.1;
  }
  .person__role {
    font-size: 17px;
    color: var(--ink);
    margin-top: 2px;
  }

  .divider {
    position: absolute;
    left: 300px;
    top: 170px;
    width: 1.5px;
    height: 110px;
    background: var(--brand-blue);
  }

  .contact {
    position: absolute;
    left: 316px;
    top: 172px;
    font-size: 13.5px;
    line-height: 1.55;
    color: var(--ink);
    list-style: none;
  }
  .contact__address { margin-bottom: 4px; }
  .contact__item { display: flex; align-items: center; gap: 6px; }
  .contact__icon { width: 11px; height: 11px; flex: none; }
</style>
</head>
<body>

<section class="card card--back" aria-label="Card back">
  <div class="brand-name">Nectra</div>
</section>

<section class="card card--front" aria-label="Card front">
  <div class="brand-name">Nectra</div>

  <div class="person">
    <div class="person__name">DANIEL REYES</div>
    <div class="person__role">Founder</div>
  </div>

  <div class="divider"></div>

  <ul class="contact">
    <li class="contact__address">418 Cedar Hollow Lane<br>Marbleton, TX 70412</li>
    <li class="contact__item">
      <svg class="contact__icon" viewBox="0 0 12 12"><path d="M3 1l2 2.5-1.2 1.2a7 7 0 0 0 3.5 3.5L8.5 7 11 9l-1.5 2C5 11 1 7 1 2.5z" fill="var(--brand-blue)"/></svg>
      0400 555 019
    </li>
    <li class="contact__item">
      <svg class="contact__icon" viewBox="0 0 12 12"><rect x="1" y="2.5" width="10" height="7" fill="none" stroke="var(--brand-blue)" stroke-width="1.2"/><path d="M1 2.5l5 4 5-4" fill="none" stroke="var(--brand-blue)" stroke-width="1.2"/></svg>
      hello@brightfieldlabs.com
    </li>
    <li class="contact__item">
      <svg class="contact__icon" viewBox="0 0 12 12"><circle cx="6" cy="6" r="5" fill="none" stroke="var(--brand-blue)" stroke-width="1.1"/><ellipse cx="6" cy="6" rx="2.2" ry="5" fill="none" stroke="var(--brand-blue)" stroke-width="1"/><path d="M1 6h10" stroke="var(--brand-blue)" stroke-width="1"/></svg>
      www.brightfieldlabs.com
    </li>
  </ul>
</section>

</body>
</html>
```